Inspirational Quotes Poster Set

Brookloft is a stylish coworking space, which has a design-oriented vintage look from the 60's with an industrial touch (www.brookloft-example.com) Brookloft Quote Poster Set of 16 posters. The poster should be typo oriented and rather simple. Reflecting a bit the clean billboard design from the sixties. Minimal / simple graphical elements

Target Market(s)

Startups and Entrepreneurs

Industry/Entity Type

Startup

Font styles to use
Sans Serif

Colors

Designer to choose colors to be used in the design.

Requirements
Must have
• Posters need to be on and very stylish

```html
<!DOCTYPE html>
<html lang="en">
<head>
<meta charset="utf-8">
<title>Brookloft Quote Poster — The Value of an Idea</title>
<link rel="stylesheet" href="https://fonts.googleapis.com/css2?family=Archivo:wdth,wght@62..125,100..900&display=swap">
<style>
  :root {
    --gold: #c9a30c;
    --ink: #000000;
    --paper: #ffffff;
  }
  html, body {
    margin: 0;
    padding: 0;
    width: 801px;
    height: 1200px;
    overflow: hidden;
    background: var(--ink);
  }
  .poster {
    display: block;
    width: 801px;
    height: 1200px;
  }
  .band-top { fill: var(--gold); }
  .field { fill: var(--ink); }
  .stripe { fill: var(--gold); }
  .quote-line {
    font-family: "Archivo", sans-serif;
    font-weight: 700;
    font-stretch: 112%;
    fill: var(--paper);
    font-size: 86px;
  }
  .keyword {
    font-family: "Archivo", sans-serif;
    font-weight: 500;
    font-stretch: 125%;
    fill: var(--paper);
    font-size: 286px;
  }
  .attribution {
    font-family: "Archivo", sans-serif;
    font-weight: 700;
    font-size: 23px;
    letter-spacing: -0.03em;
    fill: var(--paper);
  }
  .brand-name {
    font-family: "Archivo", sans-serif;
    font-weight: 600;
    font-size: 46px;
    letter-spacing: -0.04em;
    fill: var(--paper);
  }
</style>
</head>
<body>
<svg class="poster" viewBox="0 0 801 1200" xmlns="http://www.w3.org/2000/svg" role="img" aria-label="Quote poster: the value of an idea lies in the using of it">
  <rect class="field" x="0" y="0" width="801" height="1200"/>
  <rect class="band-top" x="0" y="0" width="801" height="318"/>

  <g class="stripes">
    <rect class="stripe" x="638" y="498" width="28" height="702"/>
    <rect class="stripe" x="684" y="498" width="33" height="702"/>
    <rect class="stripe" x="735" y="498" width="28" height="702"/>
  </g>

  <text class="quote-line" x="72" y="290" textLength="626" lengthAdjust="spacingAndGlyphs">the value of an</text>

  <text class="keyword" x="-8" y="535" textLength="809" lengthAdjust="spacingAndGlyphs">IDEA</text>

  <text class="quote-line" x="76" y="645" textLength="402" lengthAdjust="spacingAndGlyphs">lies in the</text>
  <text class="quote-line" x="76" y="728" textLength="422" lengthAdjust="spacingAndGlyphs">using of it</text>

  <text class="attribution" x="72" y="1040">Theo Ardmore,</text>
  <text class="attribution" x="72" y="1068">Co founder of Meridian Electric Works</text>

  <text class="brand-name" x="72" y="1141">brookloft</text>
</svg>
</body>
</html>
```